Personal Injury Law Firm needs folder design

Need a folder design for our personal injury law firm, Corrow & Talmidge, LLC. to give to all of our clients with their documents at the end of their case. I've attached our branding guide. We are branded as the 5 star law firm that fights for our clients like family. It should incorporate our colors or Green and White. We'd like to convey a message of moving on to the next chapter after finishing their case.

```html
<!DOCTYPE html>
<html lang="en">
<head>
<meta charset="utf-8">
<title>Corrow &amp; Talmidge, LLC — Client Folder Cover</title>
<link href="https://fonts.googleapis.com/css2?family=Cinzel:wght@500&family=Oswald:wght@500&display=swap" rel="stylesheet">
<style>
  :root {
    --backdrop: #dedede;
    --paper: #fafafa;
    --green: #36b985;
    --green-deep: #1ba97c;
    --green-brand: #2e9c6c;
    --yellow: #fcd804;
    --navy: #17363a;
  }
  html, body {
    margin: 0;
    width: 1200px;
    height: 3000px;
    overflow: hidden;
    background: var(--backdrop);
  }
  .canvas {
    position: relative;
    width: 1200px;
    height: 3000px;
  }
  .folder-cover {
    position: absolute;
    left: 80px;
    top: 828px;
    width: 1040px;
    height: 1343px;
    background: var(--paper);
    display: block;
  }
  .firm-name {
    font-family: "Cinzel", serif;
    font-weight: 500;
    fill: var(--green-brand);
  }
  .firm-tagline {
    font-family: "Cinzel", serif;
    font-weight: 500;
    fill: var(--navy);
    letter-spacing: 2px;
  }
  .slogan {
    font-family: "Oswald", sans-serif;
    font-weight: 500;
    fill: var(--navy);
    letter-spacing: 3px;
  }
</style>
</head>
<body>
<main class="canvas">
  <svg class="folder-cover" viewBox="0 0 751 970" xmlns="http://www.w3.org/2000/svg">
    <rect class="paper" width="751" height="970" fill="var(--paper)"/>

    <!-- firm identity -->
    <g class="firm-identity">
      <rect class="firm-square" x="67" y="67" width="105" height="86" fill="var(--green-brand)"/>
      <text class="firm-name" x="186" y="118" font-size="25" textLength="315" lengthAdjust="spacingAndGlyphs">CORROW &amp; TALMIDGE, LLC</text>
      <line x1="186" y1="79" x2="500" y2="79" stroke="var(--navy)" stroke-width="1.5"/>
      <line x1="186" y1="138" x2="258" y2="138" stroke="var(--navy)" stroke-width="1.5"/>
      <text class="firm-tagline" x="343" y="142" font-size="11" text-anchor="middle">INJURY ATTORNEYS</text>
      <line x1="428" y1="138" x2="500" y2="138" stroke="var(--navy)" stroke-width="1.5"/>
    </g>

    <!-- stepped blocks, left -->
    <polygon class="block-green-left" points="0,663 123,540 200,617 0,817" fill="var(--green-deep)"/>
    <polygon class="block-yellow-left" points="147,563 240,470 293,520 200,615" fill="var(--yellow)"/>
    <polygon class="block-navy-left" points="265,490 353,402 385,432 293,520" fill="var(--navy)"/>

    <!-- stepped blocks, right -->
    <polygon class="block-navy-right" points="497,755 587,663 617,693 527,783" fill="var(--navy)"/>
    <polygon class="block-yellow-right" points="405,820 497,730 555,788 463,880" fill="var(--yellow)"/>

    <!-- main diagonal band -->
    <polygon class="band" points="750,67 750,470 250,970 0,970 0,817" fill="var(--green)"/>
    <polygon class="block-green-right" points="250,970 405,820 485,902 415,970" fill="var(--green-deep)"/>

    <!-- slogan -->
    <g class="slogan-group" transform="translate(430,630) rotate(-45)">
      <text class="slogan" x="-118" y="-40" font-size="30">THE</text>
      <g class="rating-stars" fill="var(--yellow)">
        <path id="star" d="M0,-17 L5,-5.5 L17,-5.5 L7.5,2 L11,14 L0,7 L-11,14 L-7.5,2 L-17,-5.5 L-5,-5.5 Z" transform="translate(-95,-2)"/>
        <use href="#star" x="48"/>
        <use href="#star" x="96"/>
        <use href="#star" x="144"/>
        <use href="#star" x="192"/>
      </g>
      <text class="slogan" x="-120" y="52" font-size="44" textLength="280" lengthAdjust="spacingAndGlyphs">5-STAR LAW FIRM</text>
    </g>
  </svg>
</main>
</body>
</html>
```